Business Card and Letterhead for Pimlu - modern real estate business

I need a double sided business card design for Pimlu. Please see business card brief here https://files.trelvonadocs.com/sheet/r/7QzTmWbaXLJnoPEd-kRyUgFhHsstbvCe2qfoMxDa_pz/view?mode=shared

Please feel free to design the business cards however you feel best. I am happy to give some creative freedoms and then provide feedback from there.

Please then also create a letterhead to match the business card design

Colors

Designer to choose colors to be used in the design.

Requirements
Must have
• Must be a modern, elegant business card which looks very professional

```html
<!DOCTYPE html>
<html lang="en">
<head>
<meta charset="utf-8">
<title>Pimlu Business Card</title>
<link rel="stylesheet" href="https://fonts.googleapis.com/css2?family=Michroma&family=Open+Sans:wght@300;400&display=swap">
<style>
  :root {
    --ink: #0d1012;
    --charcoal: #2a2d30;
    --red: #f50a0a;
    --white: #ffffff;
    --paper: #ffffff;
  }
  * { margin: 0; padding: 0; box-sizing: border-box; }
  html, body { width: 923px; height: 1200px; overflow: hidden; background: var(--paper); }
  .sheet { position: relative; width: 923px; height: 1200px; }
  .card {
    position: absolute; left: 41px; width: 837px; height: 517px;
    background: var(--ink); overflow: hidden;
  }
  .card--front { top: 37px; }
  .card--back { top: 640px; }
  .edge-band {
    position: absolute; left: 0; right: 0; bottom: 0; height: 10px; background: var(--red);
  }
  .edge-rule {
    position: absolute; left: 0; right: 0; bottom: 10px; height: 3px; background: var(--charcoal);
  }
  .side-bar {
    position: absolute; top: 0; bottom: 0; width: 10px; background: var(--red);
  }
  .card--front .side-bar { left: 0; }
  .card--back .side-bar { right: 0; }
  .brand-name {
    position: absolute; font-family: "Michroma", sans-serif; color: var(--red);
    text-transform: uppercase; line-height: 1; white-space: nowrap;
  }
  .card--front .brand-name { left: 260px; top: 128px; width: 500px; text-align: center; font-size: 84px; letter-spacing: 4px; }
  .card--back .brand-name { left: 100px; top: 210px; width: 637px; text-align: center; font-size: 98px; letter-spacing: 6px; }
  .portrait {
    position: absolute; left: 32px; top: 267px; width: 184px; height: 184px;
    border-radius: 30px;
    background: linear-gradient(160deg, #8fa07a 0%, #c9c2ae 35%, #6d7456 60%, #262a30 100%);
  }
  .agent { position: absolute; left: 244px; top: 282px; color: var(--white); }
  .agent__name { font-family: "Michroma", sans-serif; font-size: 21px; letter-spacing: 1px; text-transform: uppercase; line-height: 1.2; }
  .agent__role { font-family: "Open Sans", sans-serif; font-weight: 300; font-size: 17px; margin-top: 2px; }
  .contact {
    position: absolute; top: 354px; color: var(--white);
    font-family: "Open Sans", sans-serif; font-weight: 300; font-size: 17px; line-height: 24px;
  }
  .contact--left { left: 244px; }
  .contact--right { right: 70px; text-align: right; }
  .web-line {
    position: absolute; left: 282px; width: 276px; height: 1px;
    background: linear-gradient(90deg, transparent, #cfd2d4 50%, transparent);
  }
  .web-line--top { top: 348px; }
  .web-line--bottom { top: 389px; }
  .web-address {
    position: absolute; left: 260px; top: 353px; width: 320px; text-align: center;
    font-family: "Open Sans", sans-serif; font-weight: 300; font-size: 23px; color: var(--white);
  }
  .print-label {
    position: absolute; left: 0; top: 574px; width: 923px; text-align: center;
    font-family: "Michroma", sans-serif; font-size: 34px; letter-spacing: 2px; color: #111;
  }
</style>
</head>
<body>
<main class="sheet">

  <section class="card card--front">
    <div class="side-bar"></div>
    <div class="edge-rule"></div>
    <div class="edge-band"></div>
    <div class="brand-name">Pimlu</div>
    <div class="portrait" role="img" aria-label="Portrait photo of the agent outdoors"></div>
    <div class="agent">
      <div class="agent__name">Jared Colton</div>
      <div class="agent__role">Licenced Real Estate Agent</div>
    </div>
    <div class="contact contact--left">
      <div>0412 638 905</div>
      <div>1300 555 018</div>
      <div>jared@pimlu.com</div>
    </div>
    <div class="contact contact--right">
      <div>PO Box 3917</div>
      <div>Bellhaven NSW 2791</div>
      <div>www.pimlu.com</div>
    </div>
  </section>

  <div class="print-label">READY FOR PRINT</div>

  <section class="card card--back">
    <div class="side-bar"></div>
    <div class="edge-rule"></div>
    <div class="edge-band"></div>
    <div class="brand-name">Pimlu</div>
    <div class="web-line web-line--top"></div>
    <div class="web-address">www.pimlu.com</div>
    <div class="web-line web-line--bottom"></div>
  </section>

</main>
</body>
</html>
```